Garlic Farm for Farm Sales/Restaurant sales

Need a professional, but appealing to agriculture world. We are selling 27 kinds of Organic Garlic from a farm in Simla,CO. I have uploaded logo and business information-we are going to need a template, because I will need to use it for four separate people.
-We are trying to appeal to Farm to table restaurants
-As well as growers/farmers

Target Market(s)

Agriculture Sales/Restaurants-Organic

Industry/Entity Type

Agriculture

Contact Information for Business Card

Want it to look more unique then your average kelto stock card- I want it to look amazing

Font styles to use
Sans Serif

Colors
0455a3
ec1f27
fbed22
ffffff

Requirements
Must have
• Just be creative
Nice to have
• Colorful
Should not have
• plain

```html
<!DOCTYPE html>
<html lang="en">
<head>
<meta charset="utf-8">
<title>Plains Crest Garlic — Business Card</title>
<link rel="stylesheet" href="https://fonts.googleapis.com/css2?family=Open+Sans:wght@400;600;700&display=swap">
<style>
  :root {
    --backdrop: #3a332f;
    --card-dark: #1c1c1e;
    --card-blue: #0a2f66;
    --brand-blue: #0455a3;
    --brand-blue-bright: #1a63b8;
    --brand-red: #ec1f27;
    --brand-yellow: #fbed22;
    --white: #ffffff;
    --text-light: #ececec;
    --divider: #3d3d40;
  }
  * { margin: 0; padding: 0; box-sizing: border-box; }
  html, body {
    width: 1200px; height: 844px; overflow: hidden;
    background: var(--backdrop);
    font-family: "Open Sans", Arial, sans-serif;
  }
  .canvas {
    position: relative; width: 1200px; height: 844px;
    display: flex; align-items: center; justify-content: center; gap: 50px;
  }
  .card {
    width: 520px; height: 297px; border-radius: 4px;
    box-shadow: 0 12px 30px rgba(0,0,0,.45);
    position: relative; overflow: hidden;
  }
  .card--contact { background: var(--card-dark); display: flex; }
  .card--brand {
    background: var(--card-blue);
    display: flex; align-items: center; justify-content: center;
  }

  .brand-lockup {
    display: flex; flex-direction: column; align-items: center; gap: 10px;
    text-align: center;
  }
  .brand-dot { border-radius: 50%; background: var(--brand-yellow); flex: none; }
  .brand-name { font-weight: 700; line-height: 1.05; letter-spacing: .5px; }

  .card--brand .brand-dot { width: 64px; height: 64px; }
  .card--brand .brand-name { color: var(--white); font-size: 38px; }

  .contact-brand {
    width: 260px; display: flex; align-items: center; justify-content: center;
    padding-top: 50px;
  }
  .card--contact .brand-dot { width: 54px; height: 54px; }
  .card--contact .brand-name { color: var(--brand-blue-bright); font-size: 30px; }

  .contact-details {
    padding: 40px 0 0 22px; color: var(--text-light);
    border-left: 1px solid var(--divider);
    margin: 56px 0 24px;
    padding-top: 0;
  }
  .person-name { color: var(--brand-red); font-weight: 700; font-size: 22px; line-height: 1.1; margin-top: -30px; }
  .person-role { font-size: 15px; margin: 6px 0 12px; }
  .contact-list { list-style: none; font-size: 14px; line-height: 1.5; }
  .contact-list li { display: flex; align-items: center; gap: 8px; }
  .contact-list svg { width: 12px; height: 12px; fill: var(--brand-red); flex: none; }
  .postal { font-size: 15px; line-height: 1.4; margin-top: 16px; }
</style>
</head>
<body>
<main class="canvas">
  <section class="card card--contact" aria-label="Business card, contact side">
    <div class="contact-brand">
      <div class="brand-lockup">
        <span class="brand-dot"></span>
        <span class="brand-name">plains crest<br>garlic</span>
      </div>
    </div>
    <div class="contact-details">
      <h1 class="person-name">dana merrow</h1>
      <p class="person-role">Owner</p>
      <ul class="contact-list">
        <li><svg viewBox="0 0 12 12"><path d="M1 3c0-1 1-2 2-2l1.5 2.5-1 1c.6 1.4 1.6 2.4 3 3l1-1L10 8c0 1-1 2-2 2C4 10 1 7 1 3z"/></svg>555-014-2236</li>
        <li><svg viewBox="0 0 12 12"><path d="M3 0h6v12H3zM4 1.5v8h4v-8z"/></svg>(555)-014-7</li>
        <li><svg viewBox="0 0 12 12"><path d="M0 2h12v8H0zM1 3l5 3.5L11 3z"/></svg>hello@plainscrest.com</li>
        <li><svg viewBox="0 0 12 12"><circle cx="6" cy="6" r="6"/></svg>www.plainscrest.com</li>
      </ul>
      <p class="postal">PO Box 2071,<br>Alden, CO 80999</p>
    </div>
  </section>

  <section class="card card--brand" aria-label="Business card, brand side">
    <div class="brand-lockup">
      <span class="brand-dot"></span>
      <span class="brand-name">plains crest<br>garlic</span>
    </div>
  </section>
</main>
</body>
</html>
```